Small Catering Menu

I am looking to make a small menu for catering for my company. I am thinking of a small A5 size booklet which will also have some pictures and the cover needs to be attractive.
Likely to be 8-12 pages depending upon your design (could be less or more). I need 2-3 pages as proposal concept (Cover, inside first page and one menu page) and if we like it we will make the project guaranteed before finishing the rest of the project to add security for the designer.
Pictures will be provided to the designer whose concept is the best as they are too heavy. But use generic photos for now (rather large ones) if possible.
Logo is available and so is the inside text as well as some other tidbits.
I will provide the fonts too to ensure it maintains the corporate integrity that we are following.
Industry/Entity Type
Catering

```html
<!DOCTYPE html>
<html lang="en">
<head>
<meta charset="utf-8">
<title>By the sea – Catering Menu</title>
<link rel="stylesheet" href="https://fonts.googleapis.com/css2?family=Open+Sans:wght@300;400;600&family=Tinos&display=swap">
<style>
  :root {
    --bg: #e6e6e4;
    --paper: #f7f7f6;
    --ink: #2b2b2b;
    --muted: #555;
    --red: #e0262a;
    --dark: #1c1c1c;
    --rule: #d4d4d4;
    --fresh-green: #4f7a5e;
  }
  * { box-sizing: border-box; margin: 0; padding: 0; }
  html, body { width: 1200px; height: 1000px; overflow: hidden; }
  body { background: var(--bg); font-family: "Open Sans", sans-serif; color: var(--ink); position: relative; }

  .page { position: absolute; top: 110px; width: 570px; height: 780px; background: var(--paper); overflow: hidden; }
  .page--left { left: 30px; box-shadow: -2px 3px 10px rgba(0,0,0,.15); }
  .page--right { left: 600px; box-shadow: 2px 3px 10px rgba(0,0,0,.15); }
  .spine { position: absolute; left: 598px; top: 110px; width: 4px; height: 780px; background: linear-gradient(90deg, rgba(0,0,0,.12), rgba(0,0,0,0)); }

  .title { position: absolute; left: 22px; top: 30px; font-size: 50px; font-weight: 400; letter-spacing: 1px; }
  .intro { position: absolute; left: 303px; top: 42px; font-size: 13px; line-height: 21px; color: var(--ink); }

  .section-head { position: absolute; color: var(--red); font-size: 20px; font-weight: 400; background: var(--paper); padding: 0 8px; }
  .section-rule { position: absolute; height: 1px; background: var(--rule); }

  .item { position: absolute; display: flex; align-items: flex-start; width: 510px; }
  .item__num { font-size: 28px; font-weight: 300; line-height: 1; width: 42px; }
  .item__body { flex: 0 0 260px; padding-top: 2px; }
  .item__name { font-size: 13px; line-height: 15px; }
  .item__desc { font-size: 9px; color: var(--muted); font-weight: 600; }
  .item__leader { flex: 1; border-bottom: 1px dotted #888; margin: 14px 12px 0 20px; }
  .item__price { color: var(--red); font-size: 10px; padding-top: 8px; width: 40px; }

  .mains { position: absolute; left: 0; bottom: 0; width: 570px; height: 305px; background: linear-gradient(180deg, #262626, var(--dark)); }
  .mains__title { position: absolute; top: 16px; width: 100%; text-align: center; font-family: "Tinos", serif; font-size: 22px; color: #fff; }
  .mains__rule { position: absolute; top: 30px; height: 1px; width: 170px; background: #666; }
  .dish { position: absolute; top: 70px; width: 170px; text-align: center; color: #fff; }
  .dish__photo { width: 170px; height: 92px; margin-bottom: 12px; }
  .dish__name { font-size: 12px; font-weight: 600; line-height: 16px; }
  .dish__desc { font-size: 9px; color: #777; margin-top: 4px; }
  .dish__price { color: var(--red); font-size: 12px; font-weight: 600; margin-top: 4px; }

  .desserts { position: absolute; left: 215px; top: 40px; width: 320px; height: 210px; background: #fff; border: 1px solid #cfcfcf; box-shadow: 0 2px 6px rgba(0,0,0,.15); }
  .desserts__title { position: absolute; left: 18px; top: -14px; background: #fff; padding: 0 10px; color: var(--red); font-size: 22px; }
  .sweet { position: absolute; left: 14px; display: flex; width: 290px; }
  .sweet__photo { width: 96px; height: 52px; flex: none; }
  .sweet__text { margin-left: 12px; flex: 1; }
  .sweet__name { font-size: 15px; }
  .sweet__desc { font-size: 10px; line-height: 12px; color: var(--muted); font-weight: 600; }
  .sweet__price { color: var(--red); font-size: 11px; padding-top: 22px; }

  .drinks { position: absolute; left: 10px; top: 500px; width: 420px; height: 245px; background: #fff; border: 1px solid #cfcfcf; }
  .drinks__title { position: absolute; left: 140px; top: -14px; background: #fff; padding: 0 10px; color: var(--red); font-size: 20px; }
  .drink { position: absolute; top: 20px; width: 96px; height: 212px; overflow: hidden; }
  .drink__photo { width: 100%; height: 100%; }
  .drink__label { position: absolute; left: 8px; bottom: -30px; width: 80px; height: 80px; border-radius: 50%; background: #fff; text-align: center; padding-top: 8px; }
  .drink__price { color: var(--red); font-size: 10px; }
  .drink__name { font-size: 10px; line-height: 12px; margin-top: 6px; }
  .note { position: absolute; left: 10px; top: 756px; font-size: 8.5px; color: var(--ink); }
</style>
</head>
<body>

<section class="page page--left">
  <h1 class="title">By the sea</h1>
  <p class="intro">Choose one item from each category<br>Pricing is OMR 4 per person</p>

  <div class="section-rule" style="left:20px; top:128px; width:530px;"></div>
  <h2 class="section-head" style="left:228px; top:113px;">Appetizer</h2>

  <div class="item" style="left:22px; top:160px;">
    <span class="item__num">01</span>
    <div class="item__body"><div class="item__name">Dynamite Shrimps</div><div class="item__desc">your food item description, ingredients etc..</div></div>
    <span class="item__leader"></span><span class="item__price">$4,5</span>
  </div>
  <div class="item" style="left:22px; top:215px;">
    <span class="item__num">02</span>
    <div class="item__body"><div class="item__name">Tuna Fish Cutlets.</div><div class="item__desc">your food item description, ingredients etc.. goes here</div></div>
    <span class="item__leader"></span><span class="item__price">$4,5</span>
  </div>

  <div class="section-rule" style="left:20px; top:290px; width:530px;"></div>
  <h2 class="section-head" style="left:215px; top:275px;">Sandwiches</h2>

  <div class="item" style="left:22px; top:318px;">
    <span class="item__num">04</span>
    <div class="item__body"><div class="item__name">Tuna Sanwich</div><div class="item__desc">your food item description, ingredients etc.. goes here</div></div>
    <span class="item__leader"></span><span class="item__price">$8.50</span>
  </div>
  <div class="item" style="left:22px; top:375px;">
    <span class="item__num">05</span>
    <div class="item__body"><div class="item__name">Pan Fried Baja Fish Fillet in<br>Ciabatta Bread whith Cheese</div><div class="item__desc">your food item description...</div></div>
    <span class="item__leader" style="margin-top:28px"></span><span class="item__price" style="padding-top:22px">$6.99</span>
  </div>

  <div class="mains">
    <div class="mains__rule" style="left:30px;"></div>
    <div class="mains__rule" style="left:370px;"></div>
    <h2 class="mains__title">Main Courses</h2>
    <div class="dish" style="left:18px;">
      <div class="dish__photo" role="img" aria-label="Photo of cheese wedges with cherry tomatoes" style="background:radial-gradient(circle at 45% 55%, #d9b86a, #5a3a1e 70%, #2a1a10);"></div>
      <div class="dish__name">Pan Fried Baja Fish Fillet in Ciabatta Bread whith Cheese</div>
      <div class="dish__desc">your food item description...</div>
      <div class="dish__price">$6.99</div>
    </div>
    <div class="dish" style="left:200px;">
      <div class="dish__photo" role="img" aria-label="Photo of a sliced horned melon" style="background:radial-gradient(circle at 55% 55%, #e07a2a, #7a3310 60%, #2a120a);"></div>
      <div class="dish__name">Pan Fried Baja Fish Fillet in Ciabatta Bread whith Cheese</div>
      <div class="dish__desc">your food item description...</div>
      <div class="dish__price">$6.99</div>
    </div>
    <div class="dish" style="left:382px;">
      <div class="dish__photo" role="img" aria-label="Photo of croissants on white" style="background:radial-gradient(circle at 50% 55%, #e0a050, #f3e4cf 55%, #ffffff);"></div>
      <div class="dish__name">Pan Fried Baja Fish Fillet in Ciabatta Bread whith Cheese</div>
      <div class="dish__desc">your food item description...</div>
      <div class="dish__price">$6.99</div>
    </div>
  </div>
</section>

<section class="page page--right">
  <h2 class="section-head" style="left:6px; top:30px; font-size:18px;">Salads</h2>
  <div class="item" style="left:8px; top:85px; width:200px;">
    <span class="item__num" style="font-size:20px; width:24px;">01</span>
    <div class="item__body" style="flex-basis:130px"><div class="item__name" style="font-size:10px">Dynamite Shrimps</div><div class="item__desc" style="font-size:8px">your food item description, ingredients etc..</div></div>
    <span class="item__price">$4,5</span>
  </div>
  <div class="item" style="left:8px; top:150px; width:200px;">
    <span class="item__num" style="font-size:20px; width:24px;">02</span>
    <div class="item__body" style="flex-basis:130px"><div class="item__name" style="font-size:10px">Tuna Fish Cutlets.</div><div class="item__desc" style="font-size:8px">your food item description, ingredients etc..</div></div>
    <span class="item__price">$4,5</span>
  </div>

  <aside class="desserts">
    <h2 class="desserts__title">Desserts</h2>
    <div class="sweet" style="top:30px;">
      <div class="sweet__photo" role="img" aria-label="Photo of coffee cups with leaves" style="background:radial-gradient(circle at 50% 50%, #6a8a40, #3a1e10 70%);"></div>
      <div class="sweet__text"><div class="sweet__name">Tuna Sanwich</div><div class="sweet__desc">your food item description, ingredients etc... goes here</div></div>
      <span class="sweet__price">$4,5</span>
    </div>
    <div class="sweet" style="top:115px;">
      <div class="sweet__photo" role="img" aria-label="Photo of coffee beans with herbs" style="background:radial-gradient(circle at 50% 60%, #7a4a20, #2a140a 70%);"></div>
      <div class="sweet__text"><div class="sweet__name">Tuna Sanwich</div><div class="sweet__desc">your food item description, ingredients etc... goes here</div></div>
      <span class="sweet__price">$4,5</span>
    </div>
  </aside>

  <div class="section-rule" style="left:10px; top:287px; width:540px;"></div>
  <h2 class="section-head" style="left:160px; top:272px;">Soups</h2>

  <div class="item" style="left:8px; top:320px; width:540px;">
    <span class="item__num" style="width:30px;">01</span>
    <div class="item__body"><div class="item__name" style="font-size:11px">Dynamite Shrimps</div><div class="item__desc">your food item description, ingredients etc..</div></div>
    <span class="item__leader" style="margin-top:40px"></span><span class="item__price" style="padding-top:36px">$4,5</span>
  </div>
  <div class="item" style="left:8px; top:400px; width:540px;">
    <span class="item__num" style="width:30px;">02</span>
    <div class="item__body"><div class="item__name" style="font-size:11px">Tuna Fish Cutlets.</div><div class="item__desc">your food item description, ingredients etc.. goes here</div></div>
    <span class="item__leader" style="margin-top:40px"></span><span class="item__price" style="padding-top:36px">$4,5</span>
  </div>

  <div class="drinks">
    <h2 class="drinks__title">Drinks</h2>
    <div class="drink" style="left:4px;">
      <div class="drink__photo" role="img" aria-label="Photo of a green smoothie glass with kiwi" style="background:linear-gradient(180deg, #1f3a2c, var(--fresh-green) 55%, #2a3a20);"></div>
      <div class="drink__label"><div class="drink__price">$4,5</div><div class="drink__name">Choice of Fresh Juices</div></div>
    </div>
    <div class="drink" style="left:107px;">
      <div class="drink__photo" role="img" aria-label="Photo of a green smoothie glass with kiwi" style="background:linear-gradient(180deg, #1f3a2c, var(--fresh-green) 55%, #2a3a20);"></div>
      <div class="drink__label"><div class="drink__price">$4,5</div><div class="drink__name">Soda "Fizzwell Brand" or Water</div></div>
    </div>
    <div class="drink" style="left:210px;">
      <div class="drink__photo" role="img" aria-label="Photo of a green smoothie glass with kiwi" style="background:linear-gradient(180deg, #1f3a2c, var(--fresh-green) 55%, #2a3a20);"></div>
      <div class="drink__label"><div class="drink__price">$4,5</div><div class="drink__name">Lemon Mint</div></div>
    </div>
    <div class="drink" style="left:313px;">
      <div class="drink__photo" role="img" aria-label="Photo of a green smoothie glass with kiwi" style="background:linear-gradient(180deg, #1f3a2c, var(--fresh-green) 55%, #2a3a20);"></div>
      <div class="drink__label"><div class="drink__price">$4,5</div><div class="drink__name">Iced Tea</div></div>
    </div>
  </div>
  <p class="note">Additional 10% for replacement of every item on the menu with another from outside the menu (per head)</p>
</section>

<div class="spine"></div>
</body>
</html>
```